Lumbrix Design

Looking for Lumbrix banner and square design:
Lumbrix Banner
W:1600 px H:400 px
Square
120x120

Logo attached.

Description: Data-Driven stock market portfolio management using quantitative analysis.

```html
<!DOCTYPE html>
<html lang="en">
<head>
<meta charset="UTF-8">
<title>Lumbrix – Data-Driven Portfolio Management Banner</title>
<link href="https://fonts.googleapis.com/css2?family=Barlow:wght@300;500;600;700&display=swap" rel="stylesheet">
<style>
  :root {
    --bg-blue: #17549b;
    --card-white: #fbfcfe;
    --card-tint: #eef3f9;
    --heading-blue: #0f5a9c;
    --accent-blue: #1261a8;
    --button-blue: #175aa6;
    --button-text: #ffffff;
    --pattern-tint: #c9d9ec;
    --illus-pale: #dfe6f2;
  }
  * { margin: 0; padding: 0; box-sizing: border-box; }
  html, body {
    width: 1200px; height: 400px; overflow: hidden;
    background: var(--bg-blue);
  }
  .banner {
    position: relative; width: 1200px; height: 400px;
    background: var(--bg-blue);
    font-family: "Barlow", sans-serif;
  }
  .card {
    position: absolute; left: 67px; top: 67px;
    width: 1066px; height: 266px;
    border-radius: 20px;
    background: linear-gradient(90deg, var(--card-white) 0%, var(--card-tint) 100%);
    box-shadow: 0 6px 18px rgba(0, 30, 80, 0.25);
    overflow: hidden;
  }
  .card-backdrop {
    position: absolute; left: 0; top: 0; width: 560px; height: 266px;
    background: linear-gradient(90deg, rgba(220,230,242,0.55) 0%, rgba(220,230,242,0.45) 70%, rgba(220,230,242,0) 100%);
  }
  .dot-area {
    position: absolute; left: 0; top: 48px; width: 38px; height: 75px;
    background: var(--pattern-tint); opacity: 0.6;
  }
  .ring-edge {
    position: absolute; left: -8px; top: 42px; width: 16px; height: 16px;
    border: 3px solid var(--accent-blue); border-radius: 50%;
  }
  .copy {
    position: absolute; left: 88px; top: 46px;
  }
  .headline {
    font-weight: 700; font-size: 34px; line-height: 40px;
    color: var(--heading-blue); letter-spacing: -0.2px;
  }
  .subline {
    margin-top: 2px;
    font-weight: 300; font-size: 27px; line-height: 34px;
    color: var(--heading-blue);
  }
  .cta {
    display: inline-block; margin-top: 14px;
    width: 132px; height: 40px; line-height: 40px; text-align: center;
    background: var(--button-blue); color: var(--button-text);
    font-weight: 500; font-size: 14.5px; border-radius: 2px;
    text-decoration: none;
  }
  .illustration {
    position: absolute; left: 673px; top: 36px; width: 267px; height: 212px;
    border-radius: 12px;
    background: linear-gradient(135deg, var(--illus-pale) 0%, #c9d2f0 45%, #f4c3cf 100%);
  }
  .wave-area {
    position: absolute; left: 1031px; top: 60px; width: 35px; height: 22px;
    background: var(--pattern-tint); opacity: 0.7;
  }
  .deco { position: absolute; }
</style>
</head>
<body>
<div class="banner">
  <div class="card">
    <div class="card-backdrop"></div>
    <div class="dot-area" role="img" aria-label="Decorative dot grid pattern"></div>
    <div class="ring-edge"></div>

    <div class="copy">
      <h1 class="headline">Data-Driven stock market<br>portfolio management</h1>
      <p class="subline">Using quantitative analysis</p>
      <a class="cta" href="#">Get Started</a>
    </div>

    <div class="illustration" role="img" aria-label="Isometric illustration of a person analysing a rising bar chart with an upward arrow, coins, gears and a drone"></div>

    <svg class="deco" style="left:609px;top:35px" width="24" height="14" viewBox="0 0 24 14">
      <g fill="none" stroke="var(--accent-blue)" stroke-width="2.6">
        <polyline points="1,1 7,7 1,13"/><polyline points="8,1 14,7 8,13"/><polyline points="15,1 21,7 15,13"/>
      </g>
    </svg>
    <svg class="deco" style="left:990px;top:230px" width="24" height="14" viewBox="0 0 24 14">
      <g fill="none" stroke="var(--accent-blue)" stroke-width="2.6">
        <polyline points="1,1 7,7 1,13"/><polyline points="8,1 14,7 8,13"/><polyline points="15,1 21,7 15,13"/>
      </g>
    </svg>
    <svg class="deco" style="left:922px;top:22px" width="22" height="22" viewBox="0 0 22 22">
      <circle cx="11" cy="11" r="8.5" fill="none" stroke="var(--accent-blue)" stroke-width="3.5"/>
    </svg>
    <svg class="deco" style="left:574px;top:205px" width="22" height="22" viewBox="0 0 22 22">
      <rect x="5" y="5" width="12" height="12" transform="rotate(45 11 11)" fill="none" stroke="var(--accent-blue)" stroke-width="3.5"/>
    </svg>
    <div class="wave-area" role="img" aria-label="Decorative wavy line pattern"></div>
  </div>
</div>
</body>
</html>
```